holloway paving service

Needs to have phone number 0418259730 and email markholloway@brightmail.com.au.
ABN 62318470915
name mark holloway

For all your concreting solutions
Excavation
Exposed & colour concrete
House & shed slabs
Driveways
Landing & steps

Contact Information for Business Card

ph 0418259730
email markholloway@brightmail.com.au.
ABN 62318470915
name mark holloway

```html
<!DOCTYPE html>
<html lang="en">
<head>
<meta charset="utf-8">
<title>Holloway Paving Service – Business Card</title>
<link href="https://fonts.googleapis.com/css2?family=Lato:wght@400;700&family=Montserrat:wght@600;700&display=swap" rel="stylesheet">
<style>
  :root {
    --orange: #f26a21;
    --grey: #6b6b6b;
    --grey-dark: #5a5a5a;
    --paper: #f3f3f3;
    --white: #ffffff;
    --backdrop: #e4e1dc;
  }
  * { box-sizing: border-box; margin: 0; padding: 0; }
  html, body {
    width: 1200px; height: 900px; overflow: hidden;
    background: var(--backdrop);
  }
  .sheet {
    width: 1200px; height: 900px;
    display: flex; flex-direction: column; align-items: center; justify-content: center;
    gap: 40px;
  }
  .card {
    position: relative;
    width: 700px; height: 400px;
    overflow: hidden;
    box-shadow: 0 8px 22px rgba(0,0,0,0.18);
  }

  /* Back side */
  .card--back { background: var(--orange); color: var(--white); }
  .back-brand {
    position: absolute; left: 70px; top: 150px; width: 250px;
    display: flex; align-items: center; gap: 14px;
  }
  .brand-square {
    flex: none; width: 34px; height: 34px; background: var(--white);
  }
  .back-brand .brand-name {
    font-family: "Montserrat", sans-serif; font-weight: 700;
    font-size: 19px; line-height: 1.25; letter-spacing: 0.5px;
    text-transform: uppercase; color: var(--white);
  }
  .back-divider {
    position: absolute; left: 348px; top: 90px; width: 1px; height: 220px;
    background: rgba(255,255,255,0.55);
  }
  .services {
    position: absolute; left: 380px; top: 100px;
    font-family: "Lato", sans-serif;
  }
  .services__title {
    font-family: "Montserrat", sans-serif; font-weight: 700;
    font-size: 15px; line-height: 1.25; text-transform: uppercase;
    margin-bottom: 12px;
  }
  .services__list { list-style: none; }
  .services__list li {
    font-size: 17px; line-height: 1.35;
    display: flex; align-items: center; gap: 9px;
  }
  .services__list li::before {
    content: ""; width: 7px; height: 7px; background: var(--white);
    transform: rotate(45deg); flex: none;
  }

  /* Front side */
  .card--front { background: var(--paper); }
  .swoosh { position: absolute; inset: 0; }
  .holder-name {
    position: absolute; left: 50px; top: 48px;
    font-family: "Montserrat", sans-serif; font-weight: 700;
    font-size: 22px; text-transform: uppercase; letter-spacing: 0.3px;
  }
  .holder-name__first { color: var(--orange); }
  .holder-name__last { color: var(--grey); }
  .front-brand {
    position: absolute; left: 210px; top: 100px;
    display: flex; align-items: center; gap: 16px;
  }
  .front-brand .brand-square { width: 60px; height: 60px; background: var(--orange); }
  .front-brand__rule { width: 2px; height: 90px; background: var(--orange); }
  .front-brand .brand-name {
    font-family: "Montserrat", sans-serif; font-weight: 700;
    font-size: 22px; line-height: 1.2; text-transform: uppercase;
    color: var(--orange); width: 240px;
  }
  .contact {
    position: absolute; left: 70px; top: 236px;
    font-family: "Lato", sans-serif; font-size: 19px; color: var(--grey-dark);
    list-style: none;
  }
  .contact li { display: flex; align-items: center; gap: 10px; line-height: 1.45; }
  .contact svg { width: 16px; height: 16px; flex: none; }
  .abn {
    position: absolute; right: 28px; top: 308px;
    font-family: "Lato", sans-serif; font-size: 15px; color: var(--white);
    letter-spacing: 0.3px;
  }
</style>
</head>
<body>
<main class="sheet">

  <section class="card card--back" aria-label="Business card, back">
    <div class="back-brand">
      <span class="brand-square"></span>
      <span class="brand-name">Holloway Paving Service</span>
    </div>
    <div class="back-divider"></div>
    <div class="services">
      <h2 class="services__title">For all your<br>concreting solutions</h2>
      <ul class="services__list">
        <li>Excavation</li>
        <li>Exposed &amp; colour concrete</li>
        <li>House &amp; shed slabs</li>
        <li>Driveways</li>
        <li>Landing &amp; steps</li>
      </ul>
    </div>
  </section>

  <section class="card card--front" aria-label="Business card, front">
    <svg class="swoosh" viewBox="0 0 700 400" aria-hidden="true">
      <path d="M0,345 C300,345 470,320 560,245 C620,195 660,170 700,165 L700,182 C662,187 625,210 572,258 C480,338 300,363 0,363 Z" fill="#6b6b6b"/>
      <path d="M0,371 C300,371 490,345 582,268 C630,225 665,200 700,195 L700,400 L0,400 Z" fill="#f26a21"/>
    </svg>

    <h1 class="holder-name"><span class="holder-name__first">Mark</span> <span class="holder-name__last">Holloway</span></h1>

    <div class="front-brand">
      <span class="brand-square"></span>
      <span class="front-brand__rule"></span>
      <span class="brand-name">Holloway Paving Service</span>
    </div>

    <ul class="contact">
      <li>
        <svg viewBox="0 0 16 16" aria-label="Phone"><path fill="#f26a21" d="M2 5c0-1.5 2.5-3 6-3s6 1.5 6 3v1.5h-3.2V5.2H5.2v1.3H2z M3.5 8l2-2h5l2 2v5.5h-9z"/><circle cx="8" cy="10.5" r="1.6" fill="#f3f3f3"/></svg>
        0418259730
      </li>
      <li>
        <svg viewBox="0 0 16 16" aria-label="Email"><rect x="1" y="3" width="14" height="10" rx="1" fill="#f26a21"/><path d="M1.5 3.8 8 9l6.5-5.2" fill="none" stroke="#f3f3f3" stroke-width="1.2"/></svg>
        markholloway@brightmail.com.au
      </li>
    </ul>

    <p class="abn">ABN 62318470915</p>
  </section>

</main>
</body>
</html>
```